Website design for a high-end equestrian business

Design a website to replace current one. Clean, simple, elegant design. I run a business training show jumping riders and horses, as well as buying and selling high quality horses. I run my business from a beautiful yard in Co. Kildare, Ireland. Reference to Ireland and quality sport horses is important in the website.

Current website is www.orlathornbury.com. One page in particular that I need is a "Sport Horses" page as well as a "References" page. Layout for each to be similar to this one - https://www.brackenleaze.net/en/sporthorses

Another website I like the feel of is www.topcanterstable.com
Colour theme to be charcoal grey with elements of lighter grey and cream, as per logo. Charcoal grey to be somewhat transparent, otherwise it takes over too much. Cream colour is also to be subtle and not too beige.

Please note that Thornbury is one word.

Please note there are new photographs with which to work if desired.

Sick

Target Market(s)

Upmarket clients seeking high quality coaching services and high quality show jumping horses

Number of Pages Required

2 page

Font styles to use
Serif
Sans Serif

Colors

Designer to choose only greyscale colors for use in the design.

Requirements
Must have
• A clean, simple, elegant look to the final design. OVerall theme colours must be subtle and include charcoal grey, light grey and cream. A design that will work well for mobile also. Please include only photographs provided or on the old website.
Nice to have
• artistically integrated photographs. use of the logo.
Should not have
• Anything fussy.

```html
<!DOCTYPE html>
<html lang="en">
<head>
<meta charset="utf-8">
<title>Orla Thornbury — Show Jumping &amp; Sport Horses</title>
<link href="https://fonts.googleapis.com/css2?family=Montserrat:wght@400;500;600;700&display=swap" rel="stylesheet">
<style>
:root{
  --cream:#efece4;
  --cream-line:#ddd8cc;
  --charcoal:#4a4a4a;
  --charcoal-soft:rgba(58,58,58,.88);
  --charcoal-dark:#3a3a3a;
  --ink:#222222;
  --text:#333333;
  --light:#e6e5e5;
  --search:#ebebeb;
  --white:#ffffff;
}
*{box-sizing:border-box;margin:0;padding:0}
html,body{width:1200px;height:3619px;overflow:hidden}
body{font-family:'Montserrat',sans-serif;color:var(--text);background:var(--white);position:relative}
section,header,footer,nav{position:absolute;left:0;width:1200px}
.abs{position:absolute}
.photo{position:absolute}
.section-title{position:absolute;left:0;width:1200px;text-align:center;font-size:40px;font-weight:700;color:var(--charcoal);letter-spacing:.5px}

/* header */
.site-header{top:0;height:128px;background:var(--white)}
.brand{left:90px;top:40px;display:flex;align-items:center;gap:12px;font-size:30px;font-weight:600;color:var(--charcoal)}
.brand-dot{width:22px;height:22px;border-radius:50%;background:var(--cream-line)}
.search{left:822px;top:40px;width:294px;height:52px;border-radius:26px;background:var(--search);border:2px solid #d8d8d8}
.search span{position:absolute;left:30px;top:14px;font-size:14px;color:#777}
.search-btn{position:absolute;right:6px;top:6px;width:38px;height:38px;border-radius:50%;background:var(--charcoal)}

/* nav */
.main-nav{top:128px;height:57px;background:var(--cream);border-top:1px solid var(--cream-line);border-bottom:1px solid var(--cream-line)}
.main-nav a{position:absolute;top:18px;font-size:17px;color:#3a3a3a;text-decoration:none}
.main-nav a.active{font-weight:700;color:var(--ink)}
.main-nav a.active::after{content:"";position:absolute;left:-6px;right:-6px;top:33px;height:5px;background:#6b6b6b}

/* social rail */
.social-rail{position:absolute;left:1148px;width:52px;z-index:3}
.social-rail span{display:block;width:52px;height:48px;margin-bottom:18px;background:var(--charcoal-soft);color:#fff;font-size:11px;font-weight:600;text-align:center;line-height:48px}

/* hero */
.hero{top:185px;height:560px}
.hero-photo{left:0;top:0;width:1200px;height:545px;background:linear-gradient(120deg,#5a4a3e 0%,#7d5a3c 35%,#8b5530 55%,#4d6a3a 80%,#6b7b5a 100%)}
.play{left:566px;top:209px;width:68px;height:68px;border-radius:50%;background:rgba(255,255,255,.9)}

/* about */
.about{top:745px;height:448px}
.about-photo{left:81px;top:43px;width:518px;height:320px;background:linear-gradient(135deg,#4f7a4a,#2f4f7f 60%,#c9b7a3);box-shadow:0 3px 10px rgba(0,0,0,.25)}
.about-play{left:315px;top:188px;width:50px;height:34px;border-radius:10px;background:#222}
.about h2{position:absolute;left:663px;top:42px;font-size:40px;font-weight:700;color:var(--charcoal)}
.about p{position:absolute;left:663px;top:108px;width:455px;font-size:14.5px;line-height:28px;color:var(--text)}
.btn-outline{position:absolute;left:656px;top:297px;width:209px;height:48px;border:2px solid var(--charcoal);border-radius:24px;font-size:14.5px;font-weight:600;color:var(--charcoal);text-align:center;line-height:44px}

/* horses */
.horses{top:1193px;height:642px;background:var(--cream)}
.horses .section-title{top:44px}
.tabs{position:absolute;top:134px;left:0;width:1200px;font-size:16px;font-weight:600;color:#333}
.tab{position:absolute;top:0;height:38px;line-height:38px}
.tab.active{background:var(--white);padding:0 18px;color:#555;border:1px solid var(--cream-line)}
.horse-card{position:absolute;top:213px;width:243px}
.horse-card .photo{left:0;top:0;width:243px;height:224px}
.horse-card .expand{position:absolute;right:14px;top:10px;width:22px;height:22px;border:2px solid #fff}
.horse-name{position:absolute;top:238px;left:0;width:243px;text-align:center;font-size:25px;font-weight:600;color:#333;line-height:28px}
.horse-card.featured .body{position:absolute;left:0;top:224px;width:243px;height:102px;background:var(--white)}
.horse-card.featured .name{position:absolute;left:19px;top:8px;font-size:24px;font-weight:700;color:var(--ink)}
.horse-card.featured .price{position:absolute;right:28px;top:16px;font-size:14px;color:#444}
.horse-card.featured .desc{position:absolute;left:19px;top:44px;width:210px;font-size:11px;line-height:16px;color:#555}
.arrow{position:absolute;font-size:22px;font-weight:700;color:#333}

/* sponsors */
.sponsors{top:1835px;height:322px;background:var(--white)}
.sponsors .section-title{top:57px}
.sponsor{position:absolute;top:180px;width:190px;text-align:center;font-size:18px;font-weight:600;color:var(--charcoal)}

/* gallery */
.gallery{top:2157px;height:848px;background:var(--light)}
.gallery .section-title{top:55px}
.gallery .photo{width:339px;height:295px}

/* testimonials */
.testimonials{top:3005px;height:292px;background:var(--white)}
.testimonials .section-title{top:48px}
.quote{position:absolute;left:150px;top:112px;width:900px;text-align:center;font-size:15px;line-height:28px;color:#444}
.quote-by{position:absolute;top:228px;left:0;width:1200px;text-align:center;font-size:24px;font-weight:600;color:var(--charcoal)}

/* footer */
.site-footer{top:3297px;height:273px;background:var(--charcoal)}
.site-footer h3{position:absolute;top:34px;font-size:24px;font-weight:700;color:#fff}
.links{position:absolute;left:81px;top:82px;list-style:none}
.links li{font-size:15px;color:#fff;height:33.4px}
.links li::before{content:"›";display:inline-block;width:23px;font-weight:700}
.footer-brand{position:absolute;left:418px;top:112px;width:337px;text-align:center;font-size:38px;font-weight:600;color:#fff}
.contact-list{position:absolute;left:931px;top:82px;list-style:none;font-size:15px;color:#fff}
.contact-list li{height:33.4px;display:flex;gap:10px;align-items:flex-start}
.contact-list li.indent{padding-left:24px}
.contact-list .ico{width:14px;flex:none;margin-top:2px;display:flex;justify-content:center}
.bottom-bar{position:absolute;left:0;top:3570px;width:1200px;height:49px;background:var(--charcoal-dark);color:#fff;font-size:12px}
.bottom-bar .soc{position:absolute;top:17px;font-weight:600}
.copy{position:absolute;right:90px;top:17px}
</style>
</head>
<body>

<header class="site-header">
  <div class="brand abs"><span class="brand-dot"></span>Orla Thornbury</div>
  <div class="search abs"><span>Search</span>
    <div class="search-btn"><svg width="38" height="38" viewBox="0 0 38 38"><circle cx="18" cy="18" r="5" fill="none" stroke="#fff" stroke-width="2"/><line x1="21.5" y1="21.5" x2="25" y2="25" stroke="#fff" stroke-width="2"/></svg></div>
  </div>
</header>

<nav class="main-nav">
  <a class="active" style="left:107px">About</a>
  <a style="left:202px">Horses</a>
  <a style="left:298px">Sponsors4</a>
  <a style="left:425px">Facilities &amp; Services</a>
  <a style="left:624px">Gallery</a>
  <a style="left:721px">Contact Us</a>
</nav>

<div class="social-rail" style="top:97px"><span>Feed</span><span>News</span><span>Clips</span></div>

<section class="hero">
  <div class="photo hero-photo" role="img" aria-label="Rider and horse clearing a show jump in front of a packed grandstand"></div>
  <div class="photo play"><svg width="68" height="68" viewBox="0 0 68 68"><polygon points="28,22 28,46 47,34" fill="#333"/></svg></div>
  <svg class="abs" style="left:0;top:440px" width="1200" height="120" viewBox="0 0 1200 120">
    <polygon points="0,120 0,20 600,105 1200,20 1200,120" fill="#fff"/>
    <polyline points="0,8 600,100 1200,8" fill="none" stroke="#4a4a4a" stroke-width="12"/>
  </svg>
</section>

<section class="about">
  <div class="photo about-photo" role="img" aria-label="Smiling rider in a team cap and blue show jacket"></div>
  <div class="photo about-play"><svg width="50" height="34" viewBox="0 0 50 34"><polygon points="20,10 20,24 31,17" fill="#fff"/></svg></div>
  <h2>ABOUT US</h2>
  <p>Orla is an accomplished rider, sport horse producer and equestrian coach. Following the purchase of the seven-year-old gelding “Brilliance” from Holland, at the age of just 16 Orla and he formed an exceptional partnership and successfully progressed through the ranks to the very top level of show jumping on a global scale.</p>
  <div class="btn-outline">Watch All Videos &nbsp;<svg width="14" height="10" viewBox="0 0 14 10"><rect width="14" height="10" rx="2" fill="#4a4a4a"/><polygon points="5.5,2.5 5.5,7.5 9.5,5" fill="#fff"/></svg></div>
</section>

<section class="horses">
  <h2 class="section-title">HORSES</h2>
  <div class="tabs">
    <span class="tab active" style="left:304px">Current Horses</span>
    <span class="tab" style="left:476px">|</span>
    <span class="tab" style="left:505px">Reference Horses</span>
    <span class="tab" style="left:681px">|</span>
    <span class="tab" style="left:710px">Orla’s experience</span>
  </div>

  <div class="horse-card featured" style="left:75px">
    <div class="photo" role="img" aria-label="Horse and rider schooling in a green arena" style="background:linear-gradient(180deg,#6f9a4e 0%,#4f7a3a 55%,#c8bca8 75%,#d8cdbb 100%)"></div>
    <span class="expand"></span>
    <div class="body">
      <span class="name">Ardmore</span><span class="price">Price : $ 30</span>
      <p class="desc">Sed ut perspiciatis unde omnis iste natus error sit voluptatem accusantium veritatis.</p>
    </div>
  </div>
  <div class="horse-card" style="left:344px">
    <div class="photo" role="img" aria-label="Bay horse head with bridle" style="background:linear-gradient(135deg,#3a2a20,#7a4a2c 50%,#5a8a4a)"></div>
    <span class="expand"></span><div class="horse-name">Rowan</div>
  </div>
  <div class="horse-card" style="left:614px">
    <div class="photo" role="img" aria-label="Bay horse beside its rider" style="background:linear-gradient(135deg,#7a4a2c,#5a3020 50%,#2f4a3a)"></div>
    <span class="expand"></span><div class="horse-name">BHS Emmet</div>
  </div>
  <div class="horse-card" style="left:883px">
    <div class="photo" role="img" aria-label="Horse and rider over a fence at a show" style="background:linear-gradient(180deg,#c9d3dc,#4f6f3a 45%,#6a4a30 70%,#3a4a8a)"></div>
    <span class="expand"></span><div class="horse-name">BHS Glenmore Gambit</div>
  </div>

  <span class="arrow" style="left:565px;top:572px">‹</span>
  <span class="arrow" style="left:619px;top:572px">›</span>
</section>

<section class="sponsors">
  <h2 class="section-title">SPONSORS</h2>
  <span class="arrow" style="left:107px;top:198px">‹</span>
  <div class="sponsor" style="left:160px">Seabrook Feeds</div>
  <div class="sponsor" style="left:390px">Varenta</div>
  <div class="sponsor" style="left:605px">Stridewell Ireland</div>
  <div class="sponsor" style="left:850px">Stablecraft Ireland</div>
  <span class="arrow" style="left:1087px;top:198px">›</span>
</section>

<section class="gallery">
  <h2 class="section-title">GALLERY</h2>
  <div class="photo" style="left:75px;top:142px;background:linear-gradient(135deg,#8fb0d0,#4a3020 55%,#7a98b8)" role="img" aria-label="Bay horse in a bridle against blue sky"></div>
  <div class="photo" style="left:431px;top:142px;background:linear-gradient(180deg,#e8e4da,#b79a6a 50%,#6f7a3a)" role="img" aria-label="Chestnut horse in a grassy meadow"></div>
  <div class="photo" style="left:787px;top:142px;background:linear-gradient(135deg,#c8c0b0,#8a4a2a 50%,#8a7a6a)" role="img" aria-label="Chestnut horse with blaze on a shoreline"></div>
  <div class="photo" style="left:75px;top:457px;background:linear-gradient(135deg,#bdbdbd,#2a2a2a 55%,#8a8a8a)" role="img" aria-label="Black and white portrait of a braided horse"></div>
  <div class="photo" style="left:431px;top:457px;background:linear-gradient(135deg,#a8b8a0,#1e1a18 55%,#4a6a3a)" role="img" aria-label="Dark horse against green trees"></div>
  <div class="photo" style="left:787px;top:457px;background:linear-gradient(135deg,#a06030,#c07a40 45%,#3a7aa0)" role="img" aria-label="Two chestnut horses by the sea"></div>
</section>

<section class="testimonials">
  <h2 class="section-title">TESTIMONIALS</h2>
  <span class="arrow" style="left:106px;top:130px">‹</span>
  <p class="quote">“Sed ut perspiciatis unde omnis iste natus error sit voluptatem accusantium doloremque laudantium, totam rem aperiam, eaque ipsa quae ab illo inventore veritatis et quasi architecto beatae vitae dicta sunt explicabo. Nemo enim ipsam voluptatem quia voluptas sit aspernatur aut odit aut fugit,”</p>
  <span class="arrow" style="left:1082px;top:130px">›</span>
  <div class="quote-by">- Maeve</div>
</section>

<footer class="site-footer">
  <h3 style="left:81px">Quick Links</h3>
  <ul class="links"><li>About</li><li>Horses</li><li>Sponsors4</li><li>Facilities &amp; Services</li><li>Gallery</li></ul>
  <div class="footer-brand">Orla Thornbury</div>
  <h3 style="left:931px">Contact</h3>
  <ul class="contact-list">
    <li><span class="ico"><svg width="12" height="16" viewBox="0 0 12 16"><path d="M6 0a6 6 0 0 1 6 6c0 4-6 10-6 10S0 10 0 6a6 6 0 0 1 6-6z" fill="#fff"/><circle cx="6" cy="6" r="2" fill="#4a4a4a"/></svg></span>#123 Lorium ipsum</li>
    <li class="indent">Dolor Amit.</li>
    <li><span class="ico"><svg width="14" height="14" viewBox="0 0 14 14"><path d="M3 0l3 3-2 2c1 2 3 4 5 5l2-2 3 3-2 3C6 14 0 8 0 2z" fill="#fff"/></svg></span>1-800 555 0142</li>
    <li><span class="ico"><svg width="14" height="14" viewBox="0 0 14 14"><rect x="0" y="3" width="14" height="11" fill="#fff"/><rect x="3" y="0" width="8" height="5" fill="#fff" stroke="#4a4a4a"/></svg></span>+353 555 0198</li>
  </ul>
</footer>

<div class="bottom-bar">
  <span class="soc" style="left:82px">Feed</span>
  <span class="soc" style="left:122px">News</span>
  <span class="soc" style="left:166px">Net</span>
  <span class="soc" style="left:204px">Pics</span>
  <span class="copy">© 2019 | www.companyname.com</span>
</div>

</body>
</html>
```